High-end construction company needs a business card design

We need a modern looking business card that draws people in, is memorable and looks so good people will want to sick it on their fridges.
On the first side what is needed are:
Logo
My name - Tomasz Brelwik
Title - Managing Director
Website - www.varkelt.co.uk
Email - tomasz@varkelt.co.uk
Telephone - 020 5194 6281
Mobile - 07845139072
On the back side was is needed is a list of all the services we provide:
-Kitchen Renovations
-Bathroom Renovations
-House Renovations
-Garage Conversions
-Extensions
-Loft Conversions
-Conservatories
-Carpentry
-Tiling
-Electrical
-Plumbing & Heating
-Bricklaying
-Landscaping
-Decorating
-Plastering
We would like the colours to be the same shades as on the logo with grey or black for the words.
Target Market(s)
Anyone who needs building work done
Contact Information for Business Card
This business card is for a construction company which strives to deliver excellent service and quality.
The look and feel of the card should represent this.
Requirements
Must have
- On the first side what is needed are:
Logo
My name - Tomasz Brelwik
Title - Managing Director
Website - www.varkelt.co.uk
Email - tomasz@varkelt.co.uk
Telephone - 020 5194 6281
Mobile - 07845139072
Nice to have
- Cool looking features

```html
<!DOCTYPE html>
<html lang="en">
<head>
<meta charset="utf-8">
<title>Varkelt Construction – Business Card</title>
<link rel="stylesheet" href="https://fonts.googleapis.com/css2?family=Montserrat:wght@600;700&family=Questrial&display=swap">
<style>
  :root {
    --green: #3f9634;
    --green-dark: #2f7e2a;
    --green-light: #6cc24a;
    --ink: #3b3b3b;
    --paper: #ffffff;
    --paper-shade: #ececec;
    --stage: #d9dbd9;
  }
  * { box-sizing: border-box; margin: 0; padding: 0; }
  html, body { width: 1200px; height: 900px; overflow: hidden; }
  body {
    background: var(--stage);
    font-family: "Questrial", "Century Gothic", sans-serif;
    color: var(--ink);
    position: relative;
  }
  .card {
    position: absolute;
    width: 560px;
    height: 320px;
    background: linear-gradient(120deg, var(--paper) 0%, var(--paper) 45%, var(--paper-shade) 100%);
    box-shadow: 0 10px 30px rgba(0,0,0,.18);
    overflow: hidden;
  }
  .card--back { left: 60px; top: 70px; }
  .card--front { left: 580px; top: 500px; }

  .band {
    position: absolute;
    left: 0; right: 0; bottom: 0;
    height: 26px;
    background: var(--green);
  }
  .band-rise {
    position: absolute;
    right: 0; bottom: 26px;
    width: 200px; height: 22px;
    background: var(--green);
  }
  .skyline-art {
    position: absolute;
    right: 18px; bottom: 48px;
    width: 170px; height: 130px;
    background: linear-gradient(160deg, var(--green-light) 0%, var(--green) 100%);
    border-radius: 4px 4px 0 0;
  }

  /* back side */
  .services-heading {
    position: absolute;
    left: 34px; top: 34px;
    display: flex; align-items: center; gap: 12px;
    font-family: "Montserrat", sans-serif;
    font-weight: 700;
    font-size: 20px;
    color: var(--green);
    letter-spacing: .5px;
  }
  .services-heading::after {
    content: "";
    width: 260px; height: 1.5px;
    background: var(--green);
  }
  .services-list {
    position: absolute;
    left: 44px; top: 72px;
    list-style: none;
    font-size: 15px;
    line-height: 25px;
  }
  .services-list li { display: flex; align-items: center; gap: 10px; }
  .services-list li::before {
    content: "";
    width: 9px; height: 9px;
    background: var(--green);
  }

  /* front side */
  .brand {
    position: absolute;
    left: 36px; top: 60px;
    display: flex; align-items: center; gap: 10px;
    font-family: "Montserrat", sans-serif;
    font-weight: 700;
    font-size: 22px;
    line-height: 1.05;
    color: var(--green);
    text-transform: uppercase;
  }
  .brand-mark {
    width: 14px; height: 14px;
    background: var(--green);
  }
  .person {
    position: absolute;
    right: 40px; top: 30px;
    text-align: right;
  }
  .person-name {
    font-family: "Montserrat", sans-serif;
    font-weight: 700;
    font-size: 21px;
    color: var(--green-dark);
    text-transform: uppercase;
  }
  .person-title { font-size: 14px; margin-top: 2px; }
  .contacts {
    position: absolute;
    left: 36px; top: 172px;
    list-style: none;
    font-size: 15px;
    line-height: 27px;
  }
  .contacts li { display: flex; align-items: center; gap: 10px; }
  .contacts svg { width: 15px; height: 15px; fill: none; stroke: var(--green); stroke-width: 1.8; }
</style>
</head>
<body>

<section class="card card--back" aria-label="Services side">
  <h2 class="services-heading">SERVICES</h2>
  <ul class="services-list">
    <li>Kitchen Renovations | Bathroom Renovations</li>
    <li>House Renovations | Garage Conversions</li>
    <li>Extensions | Loft Conversions</li>
    <li>Conservatories | Carpentry</li>
    <li>Tiling | Electrical</li>
    <li>Plumbing &amp; Heating | Bricklaying</li>
    <li>Landscaping | Decorating</li>
    <li>Plastering services</li>
  </ul>
  <div class="skyline-art" role="img" aria-label="Green house roof and building skyline illustration"></div>
  <div class="band-rise"></div>
  <div class="band"></div>
</section>

<section class="card card--front" aria-label="Contact side">
  <div class="brand"><span class="brand-mark"></span><span>Varkelt<br>Construction Ltd</span></div>

  <div class="person">
    <p class="person-name">Tomasz Brelwik</p>
    <p class="person-title">Managing Director</p>
  </div>

  <ul class="contacts">
    <li><svg viewBox="0 0 16 16"><rect x="4" y="1.5" width="8" height="13" rx="1.5"/><line x1="7" y1="12" x2="9" y2="12"/></svg>07845139072</li>
    <li><svg viewBox="0 0 16 16"><path d="M2 5c0-2 2-3 6-3s6 1 6 3v1h-3V5H5v1H2z"/><rect x="3" y="8" width="10" height="6" rx="1"/></svg>020 5194 6281</li>
    <li><svg viewBox="0 0 16 16"><rect x="1.5" y="3.5" width="13" height="9"/><polyline points="1.5,3.5 8,9 14.5,3.5"/></svg>tomasz@varkelt.co.uk</li>
    <li><svg viewBox="0 0 16 16"><circle cx="8" cy="8" r="6.5"/><ellipse cx="8" cy="8" rx="3" ry="6.5"/><line x1="1.5" y1="8" x2="14.5" y2="8"/></svg>www.varkelt.co.uk</li>
  </ul>

  <div class="skyline-art" role="img" aria-label="Green house roof and building skyline illustration"></div>
  <div class="band-rise"></div>
  <div class="band"></div>
</section>

</body>
</html>
```